Website redesign www.marigoldlawpc.com law firm site

Need to redesign the website that I currently have to look more modern and professional. Would also like to be able to make updates and post without having a huge hassle. See current www.marigoldlawpc.com. I just think that it looks very immature and it's very templated there's no ability for me to make posts or Add links or anything like that

Target Market(s)

California people looking for a powerhouse attorney in

Industry/Entity Type

Legal

Number of Pages Required

3 page

Font styles to use
Serif
Sans Serif

Colors
ec1f27
000000
ffffff

Requirements
Must have
• Must be mobile friendly. Must look professional and have ability to post links to other websites. Must have ability to post blogs or articles. Would like to be able to read my FeeTrove account and also have the ability to upload forms for people to download
Nice to have
• Simple design easy to use and not cluttered with too much text

```html
<!DOCTYPE html>
<html lang="en">
<head>
<meta charset="utf-8">
<title>Marigold Law, P.C — Chico California Attorney</title>
<link rel="stylesheet" href="https://fonts.googleapis.com/css2?family=Oswald:wght@400;500&family=Roboto:wght@300;400;500&display=swap">
<style>
:root{
  --red:#ec1f27;
  --red-dark:#c8161d;
  --black:#000000;
  --ink:#222222;
  --text:#555555;
  --muted:#888888;
  --white:#ffffff;
  --band:#efefef;
  --footer:#2f2f2f;
  --footer-bottom:#262626;
  --line:#dddddd;
}
*{margin:0;padding:0;box-sizing:border-box}
html,body{width:1200px;height:2568px;overflow:hidden;background:var(--white)}
body{font-family:"Roboto",Arial,sans-serif;color:var(--ink);position:relative}
.abs{position:absolute}

/* header */
.site-header{position:absolute;left:0;top:0;width:1200px;height:104px}
.brand{left:89px;top:34px;display:flex;align-items:center;gap:12px;font-family:"Roboto",Arial,sans-serif;font-weight:500;font-size:28px;color:var(--ink);line-height:1;white-space:nowrap}
.brand-mark{width:22px;height:22px;background:var(--red);display:block}
.header-phone{left:770px;top:38px;font-size:20px;color:var(--ink);display:flex;align-items:center;gap:10px}
.social-top{left:976px;top:38px;display:flex;gap:12px}
.social-top span{width:24px;height:24px;border-radius:4px;display:block}
.s1{background:#3b5ea8}.s2{background:#1da1f2}.s3{background:#1a76b4}.s4{background:#dc4a38}

/* nav */
.main-nav{left:87px;top:104px;width:1026px;height:59px;background:linear-gradient(var(--red),var(--red-dark));display:flex;z-index:3;border-radius:2px}
.main-nav a{color:var(--white);text-decoration:none;font-size:16px;line-height:59px;padding:0 32px;text-transform:uppercase}
.main-nav a.active{background:var(--black)}

/* hero */
.hero{left:0;top:142px;width:1200px;height:580px;background:linear-gradient(100deg,#c88a3a 0%,#a86b2c 40%,#5b4a3c 70%,#2e2f38 100%)}
.hero-caption{left:89px;top:548px;height:132px;background:rgba(0,0,0,.55);padding:16px 22px 0;color:var(--white);font-family:"Oswald",sans-serif;white-space:nowrap}
.hero-caption h1{font-weight:500;font-size:54px;line-height:1}
.hero-caption p{font-size:30px;margin-top:8px;line-height:1}
.hero-arrows{left:1036px;top:642px;display:flex;gap:8px}
.hero-arrows span{width:36px;height:36px;border-radius:50%;background:#111;display:flex;align-items:center;justify-content:center}

/* practice */
.section-title{font-size:27px;text-transform:uppercase;color:var(--black);font-weight:400}
.section-title em{font-style:normal;color:var(--red)}
.practice-title{left:0;top:770px;width:1200px;text-align:center}
.practice-item{display:flex;gap:20px;width:340px}
.practice-icon{width:85px;height:78px;border:1px solid var(--line);box-shadow:0 1px 4px rgba(0,0,0,.12);display:flex;align-items:center;justify-content:center;flex:none;background:var(--white)}
.practice-item h3{font-size:17px;font-weight:400;text-transform:uppercase;color:var(--ink);margin:4px 0 12px}
.practice-item p{font-size:12px;color:var(--muted);line-height:18px}

/* welcome */
.welcome{left:4px;top:1147px;width:1192px;height:356px;background:var(--band)}
.welcome h2{left:86px;top:58px;font-size:25px;font-weight:400}
.welcome h2 em{font-style:normal;color:var(--red)}
.welcome p{left:86px;top:106px;width:530px;font-size:12.5px;line-height:21px;color:var(--text);text-align:justify}
.btn-red{background:var(--red);color:var(--white);font-size:12px;text-transform:uppercase;border-radius:17px;padding:0 24px;line-height:34px;display:inline-block}
.welcome .btn-red{left:86px;top:262px}
.welcome-photo{left:647px;top:40px;width:466px;height:278px;border:4px solid var(--white);box-shadow:0 1px 5px rgba(0,0,0,.2);background:linear-gradient(135deg,#6b4a32,#3b2a20 55%,#8a6a4c)}

/* attorney band */
.attorney-band{left:0;top:1512px;width:1200px;height:339px;background:linear-gradient(90deg,#1a1a1a,#333 30%,#222 50%,#333 70%,#1a1a1a);text-align:center;color:var(--white)}
.attorney-band h2{margin-top:48px;font-size:33px;font-weight:400;text-transform:uppercase}
.attorney-band p{width:1024px;margin:22px auto 0;font-size:16px;line-height:26px;text-align:justify;text-align-last:center}
.btn-outline{display:inline-block;margin-top:36px;border:1px solid var(--white);border-radius:6px;padding:0 20px;line-height:42px;font-size:17px;text-transform:uppercase}

/* blog */
.blog-title{left:89px;top:1904px;font-size:22px}
.blog-post{left:89px;width:640px;display:flex;gap:18px}
.blog-thumb{width:184px;height:132px;flex:none}
.thumb-a{background:linear-gradient(135deg,#9fb3c8,#e9e5dc 60%,#7a8da3)}
.thumb-b{background:linear-gradient(135deg,#2b2b2b,#6d6d6d 50%,#d8d8d8)}
.blog-post h4{font-size:14px;font-weight:400;color:var(--ink)}
.blog-post .date{font-size:12px;color:var(--red);margin:8px 0 6px}
.blog-post p{font-size:11.5px;line-height:20px;color:var(--text)}
.blog-post .more{font-size:12px;color:var(--red);margin-top:6px}

/* testimonials */
.testi-title{left:788px;top:1904px;font-size:22px}
.testi-box{left:790px;top:1972px;width:322px;height:168px;background:var(--red);color:var(--white);font-size:11.5px;line-height:21px;padding:16px 18px}
.testi-tail{left:1018px;top:2140px}
.testi-avatar{left:814px;top:2160px;width:86px;height:86px;border-radius:50%;background:radial-gradient(circle at 50% 40%,#e6c7a8,#9a7457 70%,#ddd 71%)}
.testi-name{left:920px;top:2170px;font-size:14px;color:var(--muted)}
.testi-name b{font-weight:400;color:var(--text)}
.testi-nav{left:920px;top:2214px;display:flex;gap:6px}
.testi-nav span{width:22px;height:22px;border:1px solid var(--line);display:flex;align-items:center;justify-content:center}

/* footer */
.site-footer{left:0;top:2298px;width:1200px;height:210px;background:var(--footer);color:var(--white)}
.footer-col{position:absolute;top:38px}
.footer-col h5{font-size:16px;font-weight:400;text-transform:uppercase;margin-bottom:18px}
.footer-col p{font-size:12.5px;line-height:20px;color:#e4e4e4}
.contact-line{display:flex;align-items:center;gap:12px;margin-top:10px;font-size:17px}
.contact-line.small{font-size:13px;margin-top:6px}
.tweet{display:flex;gap:16px}
.tweet p{font-size:11.5px;line-height:20px}
.news-form{display:flex;margin-top:16px}
.news-form span{width:170px;height:40px;background:var(--white);color:var(--muted);font-size:11px;line-height:40px;padding-left:10px}
.news-form b{width:80px;height:40px;background:var(--red);font-weight:400;font-size:16px;line-height:40px;text-align:center}
.social-foot{display:flex;gap:16px}
.social-foot span{width:34px;height:34px;background:#e9e9e9;border-radius:3px;display:block}
.footer-bottom{left:0;top:2508px;width:1200px;height:60px;background:var(--footer-bottom);color:#ddd;font-size:13px;text-align:center;line-height:60px}
</style>
</head>
<body>

<header class="site-header">
  <div class="abs brand"><span class="brand-mark"></span>Marigold Law, P.C</div>
  <div class="abs header-phone">
    <svg width="18" height="18" viewBox="0 0 18 18"><rect width="18" height="18" rx="3" fill="#ec1f27"/><path d="M6 4.5l2 2-1 1.2c.6 1.3 1.6 2.3 2.8 2.9l1.2-1 2 2-1.2 1.4C8.5 12.8 5.2 9.5 4.6 6L6 4.5z" fill="#fff"/></svg>
    +1 555-014-2870
  </div>
  <div class="abs social-top"><span class="s1"></span><span class="s2"></span><span class="s3"></span><span class="s4"></span></div>
</header>

<nav class="abs main-nav">
  <a class="active">Home</a><a>Attorney Profile</a><a>Practice Areas</a><a>Client Reviews</a><a>Links</a><a>Contact Us</a>
</nav>

<section class="abs hero" role="img" aria-label="Photo of a team of attorneys standing in a wood-panelled courtroom"></section>
<div class="abs hero-caption"><h1>MARIGOLD LAW, P.C</h1><p>CHICO CALIFORNIA ATTORNEY</p></div>
<div class="abs hero-arrows">
  <span><svg width="12" height="12" viewBox="0 0 12 12"><path d="M8 1L3 6l5 5" stroke="#fff" stroke-width="2" fill="none"/></svg></span>
  <span><svg width="12" height="12" viewBox="0 0 12 12"><path d="M4 1l5 5-5 5" stroke="#fff" stroke-width="2" fill="none"/></svg></span>
</div>

<h2 class="abs section-title practice-title">Practice <em>Areas</em></h2>

<div class="abs practice-item" style="left:87px;top:856px">
  <div class="practice-icon"><svg width="32" height="26" viewBox="0 0 32 26"><rect x="5" y="3" width="22" height="15" fill="none" stroke="#ec1f27" stroke-width="2.5"/><rect x="1" y="20" width="30" height="3" fill="#ec1f27"/></svg></div>
  <div><h3>Business Law</h3><p>Marigold Law, P.C., we offer the following clients services to help you manage all</p></div>
</div>
<div class="abs practice-item" style="left:437px;top:856px">
  <div class="practice-icon"><svg width="30" height="26" viewBox="0 0 30 26"><path d="M15 2L2 13h4v11h7v-7h4v7h7V13h4z" fill="#ec1f27"/></svg></div>
  <div><h3>Real Estate Law</h3><p>Marigold Law, P.C., we offer the following clients services to help you manage all</p></div>
</div>
<div class="abs practice-item" style="left:793px;top:856px">
  <div class="practice-icon"><svg width="32" height="30" viewBox="0 0 32 30"><path d="M16 1L2 8h28z" fill="#ec1f27"/><rect x="3" y="9" width="26" height="2" fill="#ec1f27"/><rect x="5" y="12" width="4" height="11" fill="#ec1f27"/><rect x="14" y="12" width="4" height="11" fill="#ec1f27"/><rect x="23" y="12" width="4" height="11" fill="#ec1f27"/><rect x="2" y="24" width="28" height="4" fill="#ec1f27"/></svg></div>
  <div><h3>Bankruptcy</h3><p>Marigold Law, P.C., we offer the following clients services to help you manage all</p></div>
</div>
<div class="abs practice-item" style="left:87px;top:993px">
  <div class="practice-icon"><svg width="34" height="28" viewBox="0 0 34 28"><circle cx="17" cy="7" r="5" fill="#ec1f27"/><circle cx="7" cy="10" r="4" fill="#ec1f27"/><circle cx="27" cy="10" r="4" fill="#ec1f27"/><path d="M9 27c0-8 4-13 8-13s8 5 8 13z" fill="#ec1f27"/><path d="M1 25c0-6 3-10 6-10s4 2 4 2l-3 8z" fill="#ec1f27"/><path d="M33 25c0-6-3-10-6-10s-4 2-4 2l3 8z" fill="#ec1f27"/></svg></div>
  <div><h3>Family Law</h3><p>Marigold Law, P.C., we offer the following clients services to help you manage all</p></div>
</div>
<div class="abs practice-item" style="left:437px;top:993px">
  <div class="practice-icon"><svg width="32" height="26" viewBox="0 0 32 26"><rect x="1" y="1" width="30" height="24" fill="none" stroke="#ec1f27" stroke-width="2.5"/><rect x="1" y="1" width="30" height="5" fill="#ec1f27"/><rect x="6" y="10" width="4" height="3" fill="#ec1f27"/><rect x="12" y="10" width="14" height="3" fill="#ec1f27"/><rect x="6" y="16" width="4" height="3" fill="#ec1f27"/><rect x="12" y="16" width="14" height="3" fill="#ec1f27"/></svg></div>
  <div><h3>Criminal Law</h3><p>Marigold Law, P.C., we offer the following clients services to help you manage all</p></div>
</div>
<div class="abs practice-item" style="left:793px;top:993px">
  <div class="practice-icon"><svg width="24" height="32" viewBox="0 0 24 32"><rect x="2" y="1" width="20" height="30" fill="#ec1f27"/><g fill="#fff"><rect x="6" y="5" width="3" height="3"/><rect x="11" y="5" width="3" height="3"/><rect x="16" y="5" width="3" height="3"/><rect x="6" y="11" width="3" height="3"/><rect x="11" y="11" width="3" height="3"/><rect x="16" y="11" width="3" height="3"/><rect x="6" y="17" width="3" height="3"/><rect x="11" y="17" width="3" height="3"/><rect x="16" y="17" width="3" height="3"/><rect x="10" y="24" width="5" height="7"/></g></svg></div>
  <div><h3>Civil Litigation</h3><p>Marigold Law, P.C., we offer the following clients services to help you manage all</p></div>
</div>

<section class="abs welcome">
  <h2 class="abs">WELCOME TO <em>MARIGOLD LAW, P.C.</em></h2>
  <p class="abs">Find the big firm style legal counsel you can work with in your hometown region at Marigold Law P.C., in Chico, CA. Attorney Dana R. Whitfield, Esq., offers a boutique law firm opportunity for clients who want to enjoy all the advantages of her broad legal experience and education. She works closely with clients, and has the knowledge of many areas of law to apply to your situation. This is very helpful when it is necessary to incorporate those different areas of law practice into creating a winning argument for your unique case.</p>
  <span class="abs btn-red">Read More</span>
  <div class="abs welcome-photo" role="img" aria-label="Photo of an attorney reading law books at a desk in a library"></div>
</section>

<section class="abs attorney-band">
  <h2>Chico California Attorney</h2>
  <p>Marigold Law P.C. is owned by Dana R. Whitfield, a dedicated and caring professional who uses her broad range of skills as a California lawyer to bring consumers and business owners exceptionally strong legal representation that achieves best results. She works with people from across the northern region of California &nbsp;from the Northern border to the Central Valley region. They bring her legal concerns and problems that occur in many areas of law, including Real Estate, Family law, Business Law, Bankruptcy, Criminal Law and Civil Litigation.</p>
  <span class="btn-outline">View More</span>
</section>

<h2 class="abs section-title blog-title">Latest <em>Blog</em></h2>
<article class="abs blog-post" style="top:1966px">
  <div class="blog-thumb thumb-a" role="img" aria-label="Photo of a team meeting around a table with documents"></div>
  <div><h4>Nemo Enim Ipsam Volup</h4><div class="date">09-07-2016</div><p>Lorem Ipsum has been the industry's standard dummy text ever since the 1500s, when an unknown printer took a galley of type and scrambled it to make a type specimen book. It has survived not only five centuries,</p><div class="more">Read More »</div></div>
</article>
<article class="abs blog-post" style="top:2126px">
  <div class="blog-thumb thumb-b" role="img" aria-label="Photo of two business people shaking hands"></div>
  <div><h4>Nemo Enim Ipsam Volup</h4><div class="date">09-07-2016</div><p>Lorem Ipsum has been the industry's standard dummy text ever since the 1500s, when an unknown printer took a galley of type and scrambled it to make a type specimen book. It has survived not only five centuries,</p><div class="more">Read More »</div></div>
</article>

<h2 class="abs section-title testi-title">Testimonials</h2>
<blockquote class="abs testi-box">“ Marigold Law has met and exceeded our Expectations in assisting our company with our real estate legal needs. In an area of law where the rules our ever changing, we simply could not navigate our company effectively without their hel ”</blockquote>
<svg class="abs testi-tail" width="30" height="22" viewBox="0 0 30 22"><path d="M0 0h30L30 22z" fill="#ec1f27"/></svg>
<div class="abs testi-avatar" role="img" aria-label="Portrait photo of the client"></div>
<div class="abs testi-name">John Doe - <b>Parents Education</b></div>
<div class="abs testi-nav">
  <span><svg width="8" height="8" viewBox="0 0 8 8"><path d="M5 1L2 4l3 3" stroke="#555" fill="none"/></svg></span>
  <span><svg width="8" height="8" viewBox="0 0 8 8"><path d="M3 1l3 3-3 3" stroke="#555" fill="none"/></svg></span>
</div>

<footer class="abs site-footer">
  <div class="footer-col" style="left:92px">
    <h5>Contact Us</h5>
    <p>418 Alder Street Suite 200<br>Chico, CA 95926</p>
    <div class="contact-line"><svg width="18" height="18" viewBox="0 0 18 18"><path d="M4 1l3 3-1.5 2c.9 2 2.4 3.6 4.5 4.5l2-1.5 3 3-2 2.5C7 14 2.5 9 1.5 3.5z" fill="none" stroke="#fff" stroke-width="1.5"/></svg>(555) 014-3321</div>
    <div class="contact-line small"><svg width="18" height="14" viewBox="0 0 18 14"><rect x="1" y="1" width="16" height="12" fill="none" stroke="#fff" stroke-width="1.5"/><path d="M1 1l8 7 8-7" fill="none" stroke="#fff" stroke-width="1.5"/></svg>dana@marigoldlawgroup.com</div>
  </div>
  <div class="footer-col" style="left:372px;width:240px">
    <h5>Latest Tweet`s</h5>
    <div class="tweet">
      <svg width="16" height="16" viewBox="0 0 16 16" style="flex:none"><rect width="16" height="16" rx="2" fill="#fff"/></svg>
      <p>Phasellus porta. Fusce suscit varius mi. Cum sociis natoque penabus et magnis dis parturient montes, nascetur ridiculus mus. See more here http://t.co/Q4xLm7PzRe</p>
    </div>
  </div>
  <div class="footer-col" style="left:680px;width:260px">
    <h5>Newsletter</h5>
    <p style="font-size:11.5px">Excepteur sint occaecat cupidatat non proident, sunt in culpa qui officia deserunt mollit anim</p>
    <div class="news-form"><span>Enter your email address</span><b>Sign Up</b></div>
  </div>
  <div class="footer-col" style="left:972px">
    <h5>Social Media</h5>
    <div class="social-foot"><span></span><span></span><span></span></div>
  </div>
</footer>
<div class="abs footer-bottom">2016 &nbsp;All Rights Reserved.</div>

</body>
</html>
```